Professional violinist needs business cards

I am trying to attract the following jobs:
-private violin lessons (primarily classical)
-performance gigs (weddings, birthday parties, funerals, etc.)
-collaborations with other artists (studio recordings, performances)

I want to communicate that I have a very high standard of excellence for my work, but I also love people and celebrations.
Values/style words I like are:
love, joy, peace, fun, beauty, authenticity, excellence, warmth, refined/sleek, free spirited. If that's too confusing, just ignore :)

I will attach my favorite business card template that I could find on Canva. The lines are supposed to be like a music staff, which I think is really cool, but I also don't want it to look too busy. I like the simple black and white--I think it looks sharp--but I also am open to other ideas. I also have seen business cards with pictures included that looked great, so I attached an image that could be used as well.

I am also attaching a file that I made of my initials that could be used as a logo, but I'm not sure if it should be included.

Information on the card:
-My name (18 letters total)
-"violinist"
-phone number, email, website

Thank you!

```html
<!DOCTYPE html>
<html lang="en">
<head>
<meta charset="utf-8">
<title>Elena Whitford — Violinist Business Cards</title>
<link rel="stylesheet" href="https://fonts.googleapis.com/css2?family=Open+Sans:wght@400;700&family=Arimo:wght@400;700&display=swap">
<style>
  :root {
    --stage: #3a3a3b;
    --card-grey: #b9b2ab;
    --card-grey-light: #dcd7d2;
    --card-grey-mid: #a39c95;
    --card-grey-dark: #7d766f;
    --ink: #151515;
    --ink-soft: #2b2b2b;
    --white: #ffffff;
    --photo-brick: #7a6f62;
    --photo-brick-dark: #4e463d;
    --photo-dress: #1c1816;
    --photo-wood: #6b3f22;
    --radius: 22px;
  }
  * { box-sizing: border-box; margin: 0; padding: 0; }
  html, body {
    width: 1200px;
    height: 900px;
    overflow: hidden;
    background: var(--stage);
  }
  .stage {
    position: relative;
    width: 1200px;
    height: 900px;
  }
  .card {
    position: absolute;
    left: 300px;
    width: 600px;
    height: 343px;
    border-radius: var(--radius);
    overflow: hidden;
    box-shadow: 0 10px 24px rgba(0,0,0,0.45);
  }
  .card--back { top: 92px; }
  .card--front { top: 466px; }

  /* Back side */
  .back-photo {
    position: absolute;
    inset: 0;
    background:
      radial-gradient(ellipse 90px 70px at 74% 30%, rgba(236,232,228,0.9) 0%, transparent 100%),
      radial-gradient(ellipse 180px 90px at 28% 70%, rgba(125,118,111,0.55) 0%, transparent 100%),
      radial-gradient(ellipse 200px 70px at 45% 45%, rgba(150,142,134,0.55) 0%, transparent 100%),
      radial-gradient(ellipse 120px 110px at 90% 20%, rgba(130,123,116,0.5) 0%, transparent 100%),
      linear-gradient(160deg, var(--card-grey-dark) 0%, var(--card-grey-mid) 30%, var(--card-grey) 60%, var(--card-grey-light) 100%);
  }
  .services {
    position: absolute;
    left: 40px;
    top: 150px;
    font-family: "Open Sans", sans-serif;
    color: var(--ink);
    list-style: none;
  }
  .services li { margin-bottom: 14px; }
  .service-title {
    display: block;
    font-weight: 700;
    font-size: 19px;
    line-height: 1.15;
  }
  .service-detail {
    display: block;
    font-weight: 400;
    font-size: 16px;
    line-height: 1.2;
    color: var(--ink-soft);
  }
  .brand {
    position: absolute;
    display: flex;
    align-items: center;
    gap: 8px;
    font-family: "Open Sans", sans-serif;
    font-weight: 700;
    font-size: 18px;
    letter-spacing: 0.02em;
  }
  .brand-dot {
    width: 14px;
    height: 14px;
    border-radius: 50%;
    background: currentColor;
  }
  .brand--back { left: 380px; top: 148px; color: var(--ink); }

  /* Front side */
  .front-photo-mono {
    position: absolute;
    inset: 0;
    background:
      radial-gradient(ellipse 150px 40px at 70% 24%, rgba(60,55,50,0.55) 0%, transparent 100%),
      radial-gradient(ellipse 120px 120px at 48% 40%, rgba(140,132,124,0.5) 0%, transparent 100%),
      radial-gradient(ellipse 170px 120px at 78% 70%, rgba(235,232,228,0.75) 0%, transparent 100%),
      linear-gradient(180deg, #bdb6af 0%, #d3cec9 45%, #dcd8d3 100%);
  }
  .front-photo-portrait {
    position: absolute;
    left: 0;
    top: 112px;
    width: 262px;
    height: 231px;
    background:
      radial-gradient(ellipse 40px 55px at 62% 55%, rgba(107,63,34,0.95) 0%, transparent 100%),
      radial-gradient(ellipse 30px 35px at 48% 14%, rgba(60,40,30,0.9) 0%, transparent 100%),
      radial-gradient(ellipse 70px 150px at 58% 70%, var(--photo-dress) 0%, transparent 100%),
      linear-gradient(90deg, var(--photo-brick) 0%, var(--photo-brick-dark) 40%, #2e2824 65%, #6d6256 100%);
  }
  .brand--front {
    left: 28px;
    bottom: 26px;
    color: var(--white);
  }
  .contact {
    position: absolute;
    left: 316px;
    top: 150px;
    font-family: "Arimo", sans-serif;
    color: var(--ink);
  }
  .contact-name {
    font-weight: 700;
    font-size: 25px;
    line-height: 1.1;
  }
  .contact-role {
    font-weight: 400;
    font-size: 18px;
    margin-bottom: 8px;
  }
  .contact-list { list-style: none; }
  .contact-list li {
    display: flex;
    align-items: center;
    gap: 8px;
    font-size: 18px;
    line-height: 1.35;
  }
  .contact-list svg { width: 18px; height: 18px; flex: none; }
</style>
</head>
<body>
<main class="stage">

  <section class="card card--back" aria-label="Card back: services">
    <div class="back-photo" role="img" aria-label="Soft monochrome close-up of a violin, strings and bow with a hand plucking the strings"></div>
    <div class="brand brand--back"><span class="brand-dot"></span>Elena Whitford</div>
    <ul class="services">
      <li><span class="service-title">Private violin lessons</span><span class="service-detail">(primarily classical)</span></li>
      <li><span class="service-title">Performance gigs</span><span class="service-detail">(weddings, birthday parties, funerals, etc.)</span></li>
      <li><span class="service-title">Collaborations with other artists</span><span class="service-detail">(studio recordings, performances)</span></li>
    </ul>
  </section>

  <section class="card card--front" aria-label="Card front: contact details">
    <div class="front-photo-mono" role="img" aria-label="Soft monochrome photo of a violinist playing, bow raised across the strings"></div>
    <div class="front-photo-portrait" role="img" aria-label="Colour portrait of the violinist in a black dress holding her violin and bow against a stone brick wall"></div>
    <div class="brand brand--front"><span class="brand-dot"></span>Elena Whitford</div>
    <div class="contact">
      <h1 class="contact-name">Elena Whitford</h1>
      <p class="contact-role">Violinist</p>
      <ul class="contact-list">
        <li>
          <svg viewBox="0 0 18 18" aria-hidden="true"><rect x="1" y="1" width="16" height="16" rx="2" fill="none" stroke="#151515" stroke-width="1.5"/><path d="M6 4.5c-1 .6-1.4 1.6-1 2.8 1 3 3 5 6 6 1.2.4 2.2 0 2.8-1l-1.8-1.6-1.2.8c-1.4-.6-2.6-1.8-3.2-3.2l.8-1.2z" fill="#151515"/></svg>
          055-210 734 618
        </li>
        <li>
          <svg viewBox="0 0 18 18" aria-hidden="true"><rect x="1" y="4" width="16" height="11" fill="#151515"/><path d="M1 4l8 6 8-6" fill="none" stroke="#d8d3ce" stroke-width="1.2"/></svg>
          hello@elenawhitford.com
        </li>
        <li>
          <svg viewBox="0 0 18 18" aria-hidden="true"><circle cx="9" cy="9" r="8" fill="#151515"/><g fill="none" stroke="#d8d3ce" stroke-width="1"><ellipse cx="9" cy="9" rx="3.5" ry="8"/><path d="M1 9h16M2.5 5h13M2.5 13h13"/></g></svg>
          www.elenawhitford.com
        </li>
      </ul>
    </div>
  </section>

</main>
</body>
</html>
```